Birchpoint Studio Complementary Pass

I’d like a complimentary pass for any 30-minute Birchpoint Studio session. Choose one of the following options: Infrared Sauna with Red Light, Massage Chair Veltrafix Compression Therapy, or Paraffin Wax Hand Bath.

Please incorporate the logo and brand colors into your design. I’d like a square image that will be printed on square business cards (no rectangles).

Please refer to the logo and menu for more details.

Contact Information for Business Card

See discretion

```html
<!DOCTYPE html>
<html lang="en">
<head>
<meta charset="utf-8">
<title>Solvane Physical Therapy – Complimentary Recovery Pass</title>
<link rel="stylesheet" href="https://fonts.googleapis.com/css2?family=Kaushan+Script&family=Montserrat:wght@500;700&family=Noto+Serif:wght@400;700&display=swap">
<style>
  :root {
    --coral: #f06a4b;
    --indigo: #3b2a8e;
    --paper: #ffffff;
    --stage: #232323;
  }
  * { box-sizing: border-box; margin: 0; padding: 0; }
  html, body { width: 1200px; height: 800px; overflow: hidden; }
  body {
    background: var(--stage);
    display: flex;
    align-items: center;
    justify-content: center;
    gap: 60px;
    font-family: "Noto Serif", Georgia, serif;
  }
  .card {
    width: 520px;
    height: 520px;
    border-radius: 34px;
    position: relative;
    overflow: hidden;
  }

  /* Front */
  .card--front {
    background: var(--coral);
    display: flex;
    align-items: center;
    justify-content: center;
  }
  .brand {
    display: flex;
    align-items: center;
    gap: 14px;
  }
  .brand__dot {
    width: 22px; height: 22px;
    border-radius: 50%;
    flex: none;
  }
  .brand__name {
    font-family: "Montserrat", Arial, sans-serif;
    font-weight: 700;
    line-height: 1.05;
  }
  .brand__name small {
    display: block;
    font-size: 0.36em;
    letter-spacing: 0.18em;
    text-transform: uppercase;
    margin-top: 6px;
  }
  .card--front .brand__dot { background: var(--paper); width: 34px; height: 34px; }
  .card--front .brand__name { color: var(--paper); font-size: 72px; }

  /* Back */
  .card--back {
    background: var(--paper);
    border: 4px solid var(--coral);
    padding: 24px 34px 18px;
    color: var(--indigo);
    display: flex;
    flex-direction: column;
  }
  .card--back .brand { justify-content: center; }
  .card--back .brand__dot { background: var(--coral); }
  .card--back .brand__name { color: var(--indigo); font-size: 32px; }

  .pass-title {
    display: flex;
    align-items: center;
    gap: 10px;
    margin-top: 6px;
    width: 100%;
  }
  .pass-title::before, .pass-title::after {
    content: ""; flex: 1 1 0; min-width: 18px; height: 1.5px; background: var(--indigo);
  }
  .pass-title h1 {
    flex: none;
    font-family: "Kaushan Script", "Brush Script MT", cursive;
    font-weight: 400;
    font-size: 29px;
    line-height: 1.25;
    white-space: nowrap;
  }
  .offer {
    text-align: center;
    color: var(--coral);
    font-weight: 700;
  }
  .offer__kind { font-size: 22px; margin-top: 2px; }
  .offer__session { font-size: 17px; margin-top: 2px; }

  .options {
    list-style: none;
    margin: 8px 0 0 24px;
    font-size: 15.5px;
    line-height: 1.45;
  }
  .options li { position: relative; padding-left: 20px; }
  .options li::before {
    content: ""; position: absolute; left: 0; top: 8px;
    width: 9px; height: 9px; border-radius: 50%; background: var(--coral);
  }
  .rule { height: 1.5px; background: var(--indigo); margin: 10px 0; }
  .terms {
    text-align: right;
    font-weight: 700;
    font-size: 15px;
    line-height: 1.3;
  }

  .contact {
    margin-top: auto;
    font-family: "Montserrat", Arial, sans-serif;
    font-weight: 500;
    font-size: 12px;
  }
  .contact__name { color: var(--coral); font-weight: 700; font-size: 24px; }
  .contact__role { font-weight: 700; font-size: 14px; margin-bottom: 6px; }
  .contact__row { display: flex; justify-content: space-between; }
  .contact__item { display: flex; align-items: center; gap: 6px; margin-top: 4px; }
  .contact__item svg { width: 12px; height: 12px; fill: var(--coral); flex: none; }
  .footnote {
    color: var(--coral);
    font-size: 11.5px;
    margin-top: 4px;
  }
</style>
</head>
<body>

<section class="card card--front" aria-label="Card front">
  <div class="brand">
    <span class="brand__dot"></span>
    <p class="brand__name">Solvane<small>Physical Therapy</small></p>
  </div>
</section>

<section class="card card--back" aria-label="Card back">
  <div class="brand">
    <span class="brand__dot"></span>
    <p class="brand__name">Solvane<small>Physical Therapy</small></p>
  </div>

  <div class="pass-title"><h1>Complimentary Recovery Pass</h1></div>

  <div class="offer">
    <p class="offer__kind">A la carte</p>
    <p class="offer__session">Any 30-Minute Birchpoint Studio Session.</p>
  </div>

  <ul class="options">
    <li>Infrared Sauna with Red Light</li>
    <li>Massage Chair Veltrafix Compression Therapy</li>
    <li>Paraffin Wax Hand Bath.</li>
  </ul>

  <div class="rule"></div>
  <p class="terms">(One pass per guest.<br>By appointment only.)</p>

  <div class="contact">
    <p class="contact__name">Mira Kostelna</p>
    <p class="contact__role">Managing Director</p>
    <div class="contact__row">
      <p class="contact__item">
        <svg viewBox="0 0 24 24"><path d="M6.6 10.8a15.1 15.1 0 0 0 6.6 6.6l2.2-2.2a1 1 0 0 1 1-.25 11.4 11.4 0 0 0 3.6.57 1 1 0 0 1 1 1V20a1 1 0 0 1-1 1A17 17 0 0 1 3 4a1 1 0 0 1 1-1h3.5a1 1 0 0 1 1 1c0 1.25.2 2.46.57 3.6a1 1 0 0 1-.25 1z"/></svg>
        +469-555-0148
      </p>
      <p class="contact__item">
        <svg viewBox="0 0 24 24"><path d="M3 5h18v14H3zm2 2v.5l7 4.5 7-4.5V7zm0 2.9V17h14V9.9l-7 4.5z"/></svg>
        info@website.com
      </p>
      <p class="contact__item">
        <svg viewBox="0 0 24 24"><path d="M12 2a10 10 0 1 0 0 20 10 10 0 0 0 0-20zm0 2c.9 0 2.2 2 2.7 5H9.3C9.8 6 11.1 4 12 4zM4.3 11h3a18 18 0 0 0 0 2h-3a8 8 0 0 1 0-2zm5 0h5.4a16 16 0 0 1 0 2H9.3a16 16 0 0 1 0-2zm7.4 0h3a8 8 0 0 1 0 2h-3a18 18 0 0 0 0-2zM9.3 15h5.4c-.5 3-1.8 5-2.7 5s-2.2-2-2.7-5z"/></svg>
        www.website.com
      </p>
    </div>
    <p class="contact__item">
      <svg viewBox="0 0 24 24"><path d="M12 2a7 7 0 0 0-7 7c0 5.2 7 13 7 13s7-7.8 7-13a7 7 0 0 0-7-7zm0 9.5A2.5 2.5 0 1 1 12 6.5a2.5 2.5 0 0 1 0 5z"/></svg>
      Street, Apartment, City, State, Post Code, Country
    </p>
    <div class="rule"></div>
  </div>
  <p class="footnote">*For safety, a rest/cool-down period is required after 30 minutes in the sauna.</p>
</section>

</body>
</html>
```